Mandala Postcard Design

I am in need of a postcard to hand out at a Psychic Fair. I envision the card to having half-of-a Mandala (from my Facebook folder), touched up a bit to make it vibrant and bold. Others vendors will have cards w/photographic backgrounds doing yoga. I'd like mine to stand out for it's line-drawn "cartoonish" nature, solid-color nature. The wording would be my basic contact info and a short description ... something like: "Experience the Magic of Mandala Making ... Next Class will be held: (open space for writing, no lines) The art is contained in this Facebook folder. Lots to choose from, with my favorites being the stronger outlined designs.

https://www.examplesocial.net/Brightorbs/media_set?set=a.20462926615637197.2184852941.783542196&type=3
Updates

I just uploaded a few new drawings that might work better, since they are more round. I want to minimize the white space, for instance, avoid having the left & right corners empty. Another idea could be to use 1/4 mandalas in the corners. I'm ready to make a decision. I want it to look great, but as I gain drawing experience, I'll need to update my cards. Thanks! I'm not sure if this the place for this comment, but I'll also be needing a DVD label for my tutorials, and a front page design for a mandala coloring book.

Target Market(s)

Primarily women interested in metaphysical, psychic, meditation, reiki and a basic interest in art.

Font styles to use
Serif
Sans Serif

Requirements
Should not have
• Should not be on a dark card, really should be a plain white background, it seems, in order to stand out.

```html
<!DOCTYPE html>
<html lang="en">
<head>
<meta charset="utf-8">
<title>Mandala Making Postcard</title>
<link rel="stylesheet" href="https://fonts.googleapis.com/css2?family=Sacramento&family=Open+Sans:wght@400&display=swap">
<style>
  :root {
    --card-white: #fbfbfb;
    --ink: #3a3a3a;
    --teal: #5fbcbc;
    --blue: #5aa6dc;
    --yellow: #f2ea8a;
    --pink: #e8607a;
    --salmon: #ef8f8a;
    --violet: #9a5ab8;
  }
  html, body {
    margin: 0;
    padding: 0;
    width: 1200px;
    height: 800px;
    overflow: hidden;
    background: var(--card-white);
  }
  .postcard {
    position: relative;
    width: 1200px;
    height: 800px;
    background: var(--card-white);
    overflow: hidden;
  }
  .artwork {
    position: absolute;
    inset: 0;
    width: 1200px;
    height: 800px;
  }
  .headline {
    position: absolute;
    left: 560px;
    top: 236px;
    width: 560px;
    margin: 0;
    text-align: center;
    font-family: "Sacramento", cursive;
    font-weight: 400;
    font-size: 56px;
    line-height: 66px;
    color: var(--ink);
  }
  .class-note {
    position: absolute;
    left: 618px;
    top: 418px;
    margin: 0;
    font-family: "Open Sans", Arial, sans-serif;
    font-size: 18px;
    color: var(--ink);
  }
</style>
</head>
<body>
<main class="postcard">
  <svg class="artwork" viewBox="0 0 1200 800" xmlns="http://www.w3.org/2000/svg">
    <defs>
      <radialGradient id="half-mandala-tones" cx="0" cy="0.5" r="1">
        <stop offset="0" stop-color="#f2ea8a"/>
        <stop offset="0.45" stop-color="#5aa6dc"/>
        <stop offset="0.8" stop-color="#ef8f8a"/>
        <stop offset="1" stop-color="#5fbcbc"/>
      </radialGradient>
      <linearGradient id="corner-mandala-tones" x1="0" y1="0" x2="1" y2="1">
        <stop offset="0" stop-color="#5fbcbc"/>
        <stop offset="0.5" stop-color="#f2ea8a"/>
        <stop offset="1" stop-color="#e8607a"/>
      </linearGradient>
      <linearGradient id="butterfly-mandala-tones" x1="0" y1="0" x2="1" y2="1">
        <stop offset="0" stop-color="#5aa6dc"/>
        <stop offset="0.5" stop-color="#ef8f8a"/>
        <stop offset="1" stop-color="#f2ea8a"/>
      </linearGradient>
    </defs>

    <path class="half-mandala" role="img"
          aria-label="Colourful hand-drawn half mandala with stars, zigzags and petal border"
          d="M0 0 H300 C520 60 600 250 600 400 C600 560 520 740 300 800 H0 Z"
          fill="url(#half-mandala-tones)"/>

    <path class="corner-mandala" role="img"
          aria-label="Quarter mandala with patterned tiles and small red petals"
          d="M960 0 H1200 V215 C1120 210 1030 190 990 140 C960 100 955 50 960 0 Z"
          fill="url(#corner-mandala-tones)"/>

    <path class="butterfly-mandala" role="img"
          aria-label="Patterned winged mandala motif in blue, pink and yellow"
          d="M740 655 C800 590 900 560 1000 600 C1050 500 1120 430 1160 395 C1180 440 1200 470 1200 520 V800 H900 C960 740 840 700 740 655 Z"
          fill="url(#butterfly-mandala-tones)"/>
  </svg>

  <h1 class="headline">Experience the Magic of<br>Mandala Making</h1>
  <p class="class-note">Next Class will be held :</p>
</main>
</body>
</html>
```